Need help in designing new business card utilizing our new logo.

BuildMark Solutions works with Construction Business Owners, Managers & IT Professionals to strengthen software usage and increase user productivity.

Our Construction Accounting and Mobile Field Management Software Clients engage with us in the following areas:

New Software Implementations
Software Re-Implementations
Redesigning Software Usage at the User Level
Project Coordination & Management
Continued Software Support

Old tag line:
Weighing Options - Implementing Solutions

www.buildmark-solutions.example

Ridge 4 is a product, but not needed for a new business card.

```html
<!DOCTYPE html>
<html lang="en">
<head>
<meta charset="utf-8">
<title>BuildMark Solutions – Business Card</title>
<link rel="stylesheet" href="https://fonts.googleapis.com/css2?family=Arimo:wght@400;700&display=swap">
<style>
  :root {
    --backdrop: #2a2a2c;
    --card: #ffffff;
    --brand-blue: #2b24a8;
    --text-gray: #8a8a8e;
    --icon-fg: #ffffff;
  }
  * { margin: 0; padding: 0; box-sizing: border-box; }
  html, body {
    width: 1200px; height: 786px; overflow: hidden;
    background: var(--backdrop);
    font-family: "Arimo", Arial, sans-serif;
  }
  .stage {
    width: 1200px; height: 786px;
    display: flex; align-items: center; justify-content: center;
  }
  .business-card {
    position: relative;
    width: 735px; height: 420px;
    background: var(--card);
    box-shadow: 0 12px 36px rgba(0,0,0,.45);
  }
  .brand {
    position: absolute; left: 52px; top: 160px;
    display: flex; align-items: center; gap: 14px;
  }
  .brand-square {
    width: 34px; height: 34px; background: var(--brand-blue);
  }
  .brand-name {
    color: var(--brand-blue);
    font-weight: 700; font-size: 25px; letter-spacing: .5px;
  }
  .divider {
    position: absolute; left: 352px; top: 90px;
    width: 2px; height: 280px; background: var(--brand-blue);
  }
  .contact {
    position: absolute; left: 376px; top: 92px;
    width: 340px;
  }
  .person-name {
    color: var(--brand-blue); font-weight: 700; font-size: 25px;
  }
  .person-title {
    color: var(--text-gray); font-size: 15px; margin-top: 2px;
  }
  .address {
    color: var(--text-gray); font-size: 16px; line-height: 1.35;
    margin-top: 22px;
  }
  .contact-list { list-style: none; margin-top: 20px; }
  .contact-list li {
    display: flex; align-items: center; gap: 10px;
    color: var(--text-gray); font-size: 15px; line-height: 1;
    margin-bottom: 9px; white-space: nowrap;
  }
  .contact-icon {
    flex: 0 0 20px; width: 20px; height: 20px;
  }
</style>
</head>
<body>
<main class="stage">
  <section class="business-card" aria-label="Business card front">
    <div class="brand">
      <span class="brand-square" aria-hidden="true"></span>
      <span class="brand-name">BuildMark Solutions</span>
    </div>

    <div class="divider" aria-hidden="true"></div>

    <div class="contact">
      <h1 class="person-name">Dana R. Whitfield</h1>
      <p class="person-title">Owner</p>
      <p class="address">14B Market Lane - Suite 118<br>Riverton NY 12000</p>
      <ul class="contact-list">
        <li>
          <svg class="contact-icon" viewBox="0 0 20 20" aria-hidden="true">
            <circle cx="10" cy="10" r="10" fill="var(--brand-blue)"/>
            <path d="M7 5.5l2 2-1 1.2c.6 1.3 1.5 2.2 2.8 2.8l1.2-1 2 2-1.2 1.5C9.5 14 6 10.5 5.5 7z" fill="var(--icon-fg)"/>
          </svg>
          555-014-2281
        </li>
        <li>
          <svg class="contact-icon" viewBox="0 0 20 20" aria-hidden="true">
            <circle cx="10" cy="10" r="10" fill="var(--brand-blue)"/>
            <rect x="5" y="6.5" width="10" height="7" fill="none" stroke="var(--icon-fg)" stroke-width="1.3"/>
            <path d="M5 6.5l5 4 5-4" fill="none" stroke="var(--icon-fg)" stroke-width="1.3"/>
          </svg>
          dwhitfield@buildmark-solutions.example
        </li>
        <li>
          <svg class="contact-icon" viewBox="0 0 20 20" aria-hidden="true">
            <circle cx="10" cy="10" r="10" fill="var(--brand-blue)"/>
            <circle cx="10" cy="10" r="5" fill="none" stroke="var(--icon-fg)" stroke-width="1.2"/>
            <ellipse cx="10" cy="10" rx="2.2" ry="5" fill="none" stroke="var(--icon-fg)" stroke-width="1.1"/>
            <path d="M5 10h10" stroke="var(--icon-fg)" stroke-width="1.1"/>
          </svg>
          www.buildmark-solutions.example
        </li>
      </ul>
    </div>
  </section>
</main>
</body>
</html>
```